Talvane Aerial webdesign: Innovative Drones service company in agriculture

We need a new website according the following conditions:
• Main colour orange and current logo;
• Transparent – open – trustworthy – dynamic - personal;
• Use the smartness and overview characteristics of the crow (Talvane is Latin for crow);
• Accessible to multiple target groups and markets:
o So not too horticultural, too green;
• Use contradictions:
o Future versus nostalgia;
o Smartness crow versus precision hummingbird;
o Technology versus mechanical;
• Kestrand 2.4 LTX as a style icon?
• Long pager website
Updates

Website menu o Home o Crop monitoring  Applications Growth | Stress | Development | Diseases  Markets Breeding | Young plant | Potplants | Cutflowers | Vegetables | Soft fruit  Customer cases o Technology Aerial data collection | Artificial intelligence | Free data sets o About Vision | Company | Partners | Team | Career o Contact o News&downloads Logo: www.talvaneaerial-example.com

Target Market(s)

agriculture: owners, crop managers
oil&gas: maintenance, quality control managers and purchase managers
logistics: ware house managers, purchase managers

Industry/Entity Type

Agribusiness

Number of Pages Required

2 page

Colors
f78f20

Requirements
Must have
• long pager website
downloads
plain circle
Should not have
• Not too 'green' because first impression of designers of agriculture/horticulture is using the green colour. But that is not necessary.

Keep in mind that the current logo will be updates: the circle will be more 'general' and less 'agri'. Also the green colors in the logo will be slightly darker to make it more powerful.

```html
<!DOCTYPE html>
<html lang="en">
<head>
<meta charset="utf-8">
<title>Talvane Aerial – Fly autonomous. Monitor your crop.</title>
<link href="https://fonts.googleapis.com/css2?family=Lato:wght@300;400;700&family=Mulish:wght@400;700&display=swap" rel="stylesheet">
<style>
:root{
  --orange:#f7901e;
  --orange-text:#f59a2a;
  --slate:#6b6a6c;
  --ink:#555;
  --muted:#8a8a8a;
  --field:#d9d9d9;
  --white:#fff;
}
*{margin:0;padding:0;box-sizing:border-box}
html,body{width:1200px;height:2812px;overflow:hidden;background:var(--white)}
body{position:relative;font-family:'Lato',sans-serif;color:var(--ink)}
.abs{position:absolute}

/* header */
.brand{left:62px;top:30px;display:flex;align-items:center;gap:10px}
.brand-dot{width:44px;height:44px;border-radius:50%;background:var(--orange)}
.brand-name{font-weight:700;font-size:26px;color:var(--orange);letter-spacing:1px;line-height:1}
.main-nav{left:282px;top:46px;font-size:12.5px;font-weight:700;color:#555;letter-spacing:.2px}
.main-nav span{position:absolute;white-space:nowrap}

/* hero */
.hero-title{left:131px;top:146px;font-weight:300;font-size:38px;line-height:45px;color:var(--orange-text)}
.hero-sub{left:131px;top:254px;font-weight:300;font-size:18.5px;line-height:22.5px;color:#666}
.btn{position:absolute;display:flex;align-items:center;justify-content:center;border:2px solid #555;border-radius:18px;font-size:12px;font-weight:700;color:#555;letter-spacing:.2px}
.btn-orange{border-color:var(--orange);color:var(--orange)}
.btn-light{border-color:var(--white);color:var(--white)}
.photo{position:absolute}

/* feature bands */
.band-panel{position:absolute;color:var(--white);font-size:12.2px;line-height:15px}
.band-panel h2{font-weight:400;font-size:22px;margin-bottom:20px}
.band-panel p{margin-bottom:15px}
.panel-orange{left:637px;top:438px;width:493px;height:259px;background:var(--orange);padding:25px 48px 0 49px}
.panel-slate{left:133px;top:725px;width:504px;height:318px;background:var(--slate);padding:20px 44px 0 36px;text-align:right}

/* about */
.section-title{position:absolute;font-weight:300;font-size:37px;color:var(--orange-text)}
.about-text{font-weight:300;font-size:19px;line-height:22.5px;color:#666}

/* news */
.news-img{position:absolute;width:176px;height:176px;border:1px solid var(--orange)}
.news-body{position:absolute;left:330px;width:465px}
.news-body h3{font-weight:400;font-size:21.5px;color:#555;margin-bottom:13px}
.news-body .date{font-weight:700;font-size:14.5px;color:#555}
.news-body p{font-weight:300;font-size:14.5px;line-height:18px;color:#888}

/* contact form */
.mind-text{left:135px;top:2212px;width:335px;font-weight:300;font-size:19px;line-height:22.5px;color:#777;letter-spacing:1px}
.form-label{position:absolute;right:606px;font-weight:300;font-size:19px;color:#888;text-align:right}
.form-field{position:absolute;left:637px;width:311px;background:var(--field)}

/* footer */
.site-footer{left:62px;top:2517px;width:1068px;height:295px;background:var(--slate);color:var(--white);font-family:'Mulish',sans-serif}
.foot-col{position:absolute}
.foot-head{font-weight:700;font-size:17.5px;letter-spacing:1px}
.foot-list{font-size:15px;line-height:18px;letter-spacing:.6px}
.social-circle{position:absolute;left:86px;top:159px;width:40px;height:40px;border-radius:50%;background:var(--white)}
</style>
</head>
<body>

<header>
  <div class="abs brand">
    <div class="brand-dot"></div>
    <div class="brand-name">TALVANE</div>
  </div>
  <nav class="abs main-nav" aria-label="Main">
    <span style="left:0">HOME</span>
    <span style="left:67px">CROP MONITORING</span>
    <span style="left:224px">MARKETS</span>
    <span style="left:314px">CUSTOMER CASES</span>
    <span style="left:449px">TECHNOLOGY</span>
    <span style="left:561px">ABOUT</span>
    <span style="left:629px">CONTACTS</span>
    <span style="left:719px">NEW &amp; DOWNLOADS</span>
  </nav>
</header>

<section class="hero">
  <h1 class="abs hero-title">Fly autonomous.<br>Monitor your crop.</h1>
  <p class="abs hero-sub">Learn, improve your crop and<br>earn more.</p>
  <div class="btn btn-orange" style="left:132px;top:310px;width:133px;height:35px">FIND OUT HOW</div>
  <div class="photo" role="img" aria-label="Orange drone hovering above a greenhouse full of colourful flowers"
       style="left:687px;top:128px;width:443px;height:256px;background:linear-gradient(135deg,#c24a3a 0%,#7e9a4a 45%,#d9584a 70%,#e8a060 100%)"></div>
  <div class="photo" role="img" aria-label="Drone body with black legs and rotors"
       style="left:500px;top:150px;width:240px;height:180px;background:radial-gradient(ellipse at 60% 40%,#f28a2a 0%,#3a3a3a 45%,rgba(255,255,255,0) 70%)"></div>
</section>

<section class="features">
  <div class="photo" role="img" aria-label="Drone flying through a greenhouse above rows of plants, with yellow guide lines"
       style="left:133px;top:438px;width:504px;height:259px;background:linear-gradient(180deg,#d8dcdc 0%,#b9bfbf 28%,#4f7a2e 45%,#3d6a24 75%,#5a3f2a 100%)"></div>
  <div class="band-panel panel-orange">
    <h2>Crop Monitoring</h2>
    <p>Using drones in greenhouses opens up opportunities to optimize the growth process. With the Talvane drone a wide variety of data can be collected, which is analyzed using advanced Artificial Intelligence algorithms.</p>
    <p style="margin:0">The information obtained by this is invaluable to the grower.<br>Talvane Aerial developed a unique system which makes it possible for a drone to fly autonomous inside a greenhouse and collects the right data at the right positions.<br>Together with the vision algorithm and user interface this system will be delivered as a ready for use product.</p>
  </div>

  <div class="band-panel panel-slate">
    <h2>Technology</h2>
    <p>The Talvane Aerial uses a smart navigation system in order to fly complete autonomous. The drone is equipped with camera’s and other sensors. Depending on the application this is an RGB camera or a multispectral camera. Other sensors can be temperature, light and CO2.</p>
    <p>The data is analyzed using Artificial intelligence algorithms, such as Deep Learning. For collected images this means that the algorithm can ‘see’ the growth status and whether there are problems with the plants. After its flight the drone sends the collected data to a server, where the analysis takes place. The results are presented to the grower in a user-friendly way on its smartphone, tablet or PC.</p>
  </div>
  <div class="btn btn-light" style="left:455px;top:984px;width:133px;height:35px">LEARN MORE</div>
  <div class="photo" role="img" aria-label="Orange drone hovering inside a greenhouse"
       style="left:637px;top:725px;width:493px;height:318px;background:radial-gradient(ellipse at 50% 55%,#e07a2a 0%,#555 30%,#9ea3a3 60%,#c8cccc 100%)"></div>
</section>

<section class="about">
  <h2 class="section-title" style="left:138px;top:1110px">About Us</h2>
  <p class="abs about-text" style="left:133px;top:1190px;width:465px">The Talvane Aerial uses a smart navigation system in order to fly complete autonomous. The drone is equipped with camera’s and other sensors. Depending on the application this is an RGB camera or a multispectral camera. Other sensors can be temperature, light and CO2.</p>
  <p class="abs about-text" style="left:640px;top:1129px;width:445px">The data is analyzed using Artificial intelligence algorithms, such as Deep Learning. For collected images this means that the algorithm can ‘see’ the growth status and whether there are problems with the plants. After its flight the drone sends the collected data to a server, where the analysis takes place. The results are presented to the grower in a user-friendly way on its smartphone, tablet or PC.</p>
  <div class="btn" style="left:640px;top:1319px;width:133px;height:35px">LEARN MORE</div>
</section>

<section class="news">
  <h2 class="section-title" style="left:138px;top:1404px">News &amp; Downloads</h2>

  <div class="news-img" role="img" aria-label="Front of an orange Kestrand 2.4 LTX classic car" style="left:131px;top:1473px;background:linear-gradient(160deg,#e7e3dc 0%,#ef6a2a 40%,#c84d1e 70%,#3a3a3a 100%)"></div>
  <div class="news-body" style="top:1470px">
    <h3>Lorem Ipsum set dolor consectatur</h3>
    <div class="date">July 30, 2020</div>
    <p>The Talvane Aerial uses a smart navigation system in order to fly complete autonomous. The drone is equipped with camera’s and other sensors. Depending on the application this is an RGB camera or a multi-spectral camera. Other sensors can be temperature, light and CO2.</p>
  </div>
  <div class="btn" style="left:332px;top:1615px;width:133px;height:35px">READ MORE</div>

  <div class="news-img" role="img" aria-label="Drone standing on green grass" style="left:131px;top:1678px;background:linear-gradient(180deg,#6e9a3a 0%,#5d8a30 45%,#e07a2a 55%,#4f7a2a 100%)"></div>
  <div class="news-body" style="top:1675px">
    <h3>Lorem Ipsum set dolor consectatur</h3>
    <div class="date">July 30, 2020</div>
    <p>The Talvane Aerial uses a smart navigation system in order to fly complete autonomous. The drone is equipped with camera’s and other sensors. Depending on the application this is an RGB camera or a multi-spectral camera. Other sensors can be temperature, light and CO2.</p>
  </div>
  <div class="btn" style="left:332px;top:1820px;width:133px;height:35px">READ MORE</div>

  <div class="news-img" role="img" aria-label="Glowing yellow data bar charts on a purple background" style="left:131px;top:1889px;background:linear-gradient(160deg,#c99a20 0%,#e8c030 35%,#9a6a3a 65%,#6a3a8a 100%)"></div>
  <div class="news-body" style="top:1887px">
    <h3>Latest Aerial Data sets now available</h3>
    <div class="date">July 30, 2020</div>
    <p>The Talvane Aerial uses a smart navigation system in order to fly complete autonomous. The drone is equipped with camera’s and other sensors. Depending on the application this is an RGB camera or a multi-spectral camera. Other sensors can be temperature, light and CO2.</p>
  </div>
  <div class="btn" style="left:332px;top:2032px;width:133px;height:35px">DOWNLOAD NOW</div>
</section>

<section class="contact">
  <h2 class="section-title" style="left:132px;top:2138px;letter-spacing:1px">What’s on your mind?</h2>
  <div class="abs mind-text">
    <p>Curabitur ornare vitae sem nec tempus. Morbi laoreet metus neque, eu hendrerit magna interdum a. Aliquam erat volutpat. Nam auctor ut augue eu varius.</p>
    <p style="margin-top:22px">Cras elementum accumsan pellentesque. Mauris nec nisi id ante faucibus consectetur. Aenean ornare aliquet neque, a fermentum odio vulputate sed.</p>
  </div>
  <div class="form-label" style="top:2212px">Email</div>
  <div class="form-label" style="top:2242px">First Name</div>
  <div class="form-label" style="top:2272px">Last Name</div>
  <div class="form-label" style="top:2302px">Message</div>
  <div class="form-field" style="top:2221px;height:21px"></div>
  <div class="form-field" style="top:2248px;height:21px"></div>
  <div class="form-field" style="top:2275px;height:21px"></div>
  <div class="form-field" style="top:2303px;height:61px"></div>
  <div class="btn" style="left:640px;top:2390px;width:133px;height:35px">SEND</div>
</section>

<footer class="abs site-footer">
  <div class="foot-col" style="left:78px;top:20px">
    <div class="foot-head">WHY DON’T YOU DROP BY?</div>
    <div class="foot-list" style="margin-top:22px">Lindeboomlaan 14B,<br>4821PK, Veldhoven<br>Email: info@talvaneaerial-example.com<br>Telephone: +31 6 12 34 56 78</div>
  </div>
  <div class="social-circle" role="img" aria-label="Social profile link"></div>

  <div class="foot-col" style="left:418px;top:20px">
    <div class="foot-head">CROP MONITORING</div>
    <div class="foot-list">Growth<br>Stress<br>Development<br>Diseases</div>
  </div>
  <div class="foot-col" style="left:418px;top:145px">
    <div class="foot-head">MARKETS</div>
    <div class="foot-list">Breeding<br>Young plant<br>Potplants<br>Cutflowers<br>Vegetables<br>Soft fruit</div>
  </div>

  <div class="foot-col" style="left:628px;top:20px">
    <div class="foot-head">TECHNOLOGY</div>
    <div class="foot-list">Aerial data collection<br>Artificial intelligence<br>Free data sets</div>
  </div>
  <div class="foot-col foot-head" style="left:628px;top:145px">NEWS &amp; DOWNLOADS</div>
  <div class="foot-col foot-head" style="left:628px;top:196px">CUSTOMER CASES</div>

  <div class="foot-col" style="left:869px;top:20px">
    <div class="foot-head">ABOUT</div>
    <div class="foot-list">Vision<br>Company<br>Partners<br>Team<br>Career</div>
  </div>
  <div class="foot-col foot-head" style="left:869px;top:145px">FREE DATA SETS</div>
  <div class="foot-col foot-head" style="left:869px;top:196px">CONTACT</div>
</footer>

</body>
</html>
```